Business Card Design - Photographer

I am a landscape photographer and I require a business card design. 

I require two designs:
1)  a double sided business card
 and
b)  a single sided business card 

The single sided design can either be the same as the double sided (with just one side having all the information)....or it can be an entire new design. Its up to you.

My corporate colours are (CMYK):

Blue   69, 32, 0, 0
Grey  72,  64,  47,  31
Green  32,  2,  91,  0
Yellow   0, 19, 92, 0
Orange  0, 39, 75, 0

Colour space in final file should be in CMYK.

The details that need to be included on the card:

- Use the provided Logo
- Name: Wiktor Baranowski
- Email:   sales@vistalumeworks.com.au
- Website:    vistalumeworks.com.au
- Twitter:    twitter.com/vistalumeworks
- Facebook:   facebook.com/vistalumeworks
- Mobile  0417 539 662

Please use the attached template to design the logo to the specified size, including the marked bleed lines. I have also attached my logo in PNG (transparent background) and ai format for you to use.

The final file should be:
- Photoshop version with layers so I can edit the name/text etc. All non vector files should be high resolution at 1039 x 697 pixels at 300 dpi.

I also require a file as:
- Vector based PDF

Anyway questions please contact me.

Thank you

Industry/Entity Type

Landscape

Logo styles of interest
Pictorial/Combination Logo
Abstract Logo
Wordmark Logo
Lettermark Logo
Requirements
Must have
• The details that need to be included on the card:

- Use the provided Logo
- Name: Wiktor Baranowski
- Email: sales@vistalumeworks.com.au
- Website: vistalumeworks.com.au
- Twitter: twitter.com/vistalumeworks
- Facebook: facebook.com/vistalumeworks
- Mobile 0417 539 662

```html
<!DOCTYPE html>
<html lang="en">
<head>
<meta charset="utf-8">
<title>Vistalume Works – Business Card</title>
<link rel="stylesheet" href="https://fonts.googleapis.com/css2?family=Cinzel:wght@400;600&family=Tinos&family=Lato:wght@400&display=swap">
<style>
  :root {
    --backdrop: #c58a52;
    --card-white: #ffffff;
    --slate: #3c3f52;
    --brand-blue: #4a94cf;
    --brand-orange: #f5a44a;
    --ink: #3c3f52;
    --ink-soft: #555a6b;
    --on-dark: #ffffff;
  }
  * { margin: 0; padding: 0; box-sizing: border-box; }
  html, body { width: 1200px; height: 388px; overflow: hidden; }
  body { background: var(--backdrop); position: relative; }

  .card {
    position: absolute;
    top: 42px;
    width: 526px;
    height: 299px;
    overflow: hidden;
    box-shadow: 0 1px 3px rgba(0,0,0,.25);
  }
  .card--front { left: 58px; background: var(--card-white); }
  .card--back  { left: 623px; background: var(--slate); }

  .wave-band {
    position: absolute;
    left: 0;
    top: 178px;
    width: 526px;
    height: 121px;
    background: linear-gradient(100deg, #4f7fae 0%, var(--slate) 42%, var(--slate) 78%, #6a5d55 100%);
  }

  .mark-dot {
    position: absolute;
    border-radius: 50%;
  }
  .card--front .mark-dot { left: 102px; top: 15px; width: 88px; height: 88px; background: var(--slate); }
  .card--back  .mark-dot { left: 214px; top: 56px; width: 90px; height: 90px; background: var(--on-dark); }

  .brand-name {
    position: absolute;
    font-family: "Cinzel", serif;
    font-weight: 400;
    font-size: 23px;
    line-height: 28px;
    letter-spacing: .3px;
    white-space: nowrap;
    text-align: center;
  }
  .brand-name::after {
    content: "";
    position: absolute;
    left: 50%;
    bottom: -3px;
    width: 238px;
    margin-left: -119px;
    border-top: 1px solid currentColor;
  }
  .card--front .brand-name { left: 27px; top: 113px; width: 240px; color: var(--ink); }
  .card--back  .brand-name { left: 0; top: 162px; width: 526px; color: var(--on-dark); }

  .tagline {
    position: absolute;
    font-family: "Cinzel", serif;
    font-weight: 600;
    font-size: 9.5px;
    letter-spacing: 1.6px;
    white-space: nowrap;
    text-align: center;
  }
  .card--front .tagline { left: 27px; top: 146px; width: 240px; color: var(--ink); }
  .card--back  .tagline { left: 0; top: 196px; width: 526px; color: var(--on-dark); }

  .address {
    position: absolute;
    right: 31px;
    top: 21px;
    text-align: right;
    font-family: "Tinos", serif;
    font-style: normal;
    font-size: 13px;
    line-height: 18px;
    color: var(--ink-soft);
  }

  .contacts {
    position: absolute;
    right: 19px;
    top: 192px;
    list-style: none;
    font-family: "Tinos", serif;
    font-size: 13px;
    line-height: 18.6px;
    color: var(--on-dark);
    text-align: right;
  }
  .contacts li { display: flex; justify-content: flex-end; align-items: center; gap: 5px; }
  .contacts svg { width: 9px; height: 9px; flex: none; }
  .contacts .square { width: 8px; height: 8px; background: #cfd6e2; flex: none; }

  .website {
    position: absolute;
    left: 0; top: 244px; width: 526px;
    text-align: center;
    font-family: "Lato", sans-serif;
    font-size: 13px;
    letter-spacing: 1.8px;
    color: var(--on-dark);
  }
</style>
</head>
<body>

  <section class="card card--front">
    <div class="wave-band" role="img" aria-label="Flowing blue, orange and slate wave artwork"></div>

    <div class="mark-dot"></div>
    <div class="brand-name">VISTALUME WORKS</div>
    <div class="tagline">FINE ART PHOTOGRAPHY</div>

    <address class="address">00, Complex Name<br>State Name, City 0020</address>

    <ul class="contacts">
      <li>
        <svg viewBox="0 0 10 10"><rect x="2" y="0.5" width="6" height="9" rx="1" fill="#fff"/><rect x="3" y="1.8" width="4" height="5" fill="var(--slate)"/></svg>
        0417 539 662
      </li>
      <li>
        <svg viewBox="0 0 10 10"><rect x="0.5" y="2" width="9" height="6" fill="#fff"/><path d="M0.5 2 L5 5.5 L9.5 2" fill="none" stroke="var(--slate)" stroke-width="0.9"/></svg>
        sales@vistalumeworks.com.au
      </li>
      <li>
        <svg viewBox="0 0 10 10"><circle cx="5" cy="5" r="4.3" fill="#fff"/><path d="M0.7 5 H9.3 M5 0.7 C2.5 3 2.5 7 5 9.3 M5 0.7 C7.5 3 7.5 7 5 9.3" fill="none" stroke="var(--slate)" stroke-width="0.7"/></svg>
        www.vistalumeworks.com.au
      </li>
      <li><span class="square"></span>vistalumeworks</li>
      <li><span class="square"></span>vistalumeworks</li>
    </ul>
  </section>

  <section class="card card--back">
    <div class="mark-dot"></div>
    <div class="brand-name">VISTALUME WORKS</div>
    <div class="tagline">FINE ART PHOTOGRAPHY</div>
    <div class="website">www.vistalumeworks.com.au</div>
  </section>

</body>
</html>
```